BOLD & MINIMALIST DESIGN NEEDED

We want a very bold but minimalistic business card design that is impactful and utilizes both sides of the business card. Our current logo is included for your use.

We want bold fonts and good use of negative space. We don't want the logo to overpower the design.

Target Market(s)

Professionals who are building new commercial buildings.

Industry/Entity Type

Construction

Contact Information for Business Card

Name, Title, email, office phone, cell phone, website

Font styles to use
Serif
Sans Serif

Requirements
Must have
• Bold design!

```html
<!DOCTYPE html>
<html lang="en">
<head>
<meta charset="utf-8">
<title>Ridgeline Design + Build – Business Card</title>
<link rel="stylesheet" href="https://fonts.googleapis.com/css2?family=Roboto:wght@400;500;700;900&display=swap">
<style>
  :root {
    --bg-top: #d6d6d6;
    --bg-bottom: #a9a9a9;
    --card-white: #ffffff;
    --card-black: #161616;
    --ink: #1b1b1b;
    --ink-soft: #3a3a3a;
    --accent: #8cc63f;
    --rule: #4a4a4a;
    --emboss: #2a2a2a;
    --emboss-light: #3c3c3c;
  }
  * { box-sizing: border-box; margin: 0; padding: 0; }
  html, body { width: 1200px; height: 802px; overflow: hidden; }
  body {
    background: linear-gradient(180deg, var(--bg-top), var(--bg-bottom));
    font-family: "Roboto", Arial, sans-serif;
    position: relative;
  }
  .card {
    position: absolute;
    width: 530px;
    height: 302px;
    border-radius: 20px;
    overflow: hidden;
    box-shadow: 0 14px 30px rgba(0,0,0,.28);
  }
  .card--front { left: 48px; top: 250px; background: var(--card-white); }
  .card--back { left: 622px; top: 250px; background: var(--card-black); }

  /* front */
  .brand {
    position: absolute;
    right: 40px;
    top: 46px;
    display: flex;
    align-items: center;
    gap: 10px;
  }
  .brand__mark { width: 18px; height: 18px; background: var(--accent); }
  .brand__name {
    font-weight: 900;
    font-size: 20px;
    letter-spacing: .5px;
    color: var(--ink);
    text-transform: uppercase;
  }
  .person { position: absolute; left: 34px; top: 150px; }
  .person__name { font-weight: 700; font-size: 24px; color: var(--accent); line-height: 1.1; }
  .person__title { font-size: 15px; color: var(--ink-soft); margin-top: 4px; }
  .divider {
    position: absolute;
    left: 34px; right: 40px; top: 210px;
    border-top: 1.5px solid var(--rule);
  }
  .contacts {
    position: absolute;
    left: 34px; right: 40px; top: 222px;
    display: flex;
    justify-content: space-between;
    font-size: 12.5px;
    color: var(--ink);
  }
  .contacts__col { display: flex; flex-direction: column; gap: 6px; }
  .contact { display: flex; align-items: center; gap: 7px; white-space: nowrap; }
  .contact svg { width: 13px; height: 13px; flex: none; fill: var(--ink); }
  .edge-band {
    position: absolute;
    left: 0; right: 0; bottom: 0; height: 10px;
    background: linear-gradient(90deg, var(--ink) 0 48%, var(--accent) 48% 100%);
  }

  /* back */
  .back-brand {
    position: absolute;
    inset: 0;
    display: flex;
    align-items: center;
    justify-content: center;
    gap: 14px;
  }
  .back-brand__mark { width: 30px; height: 30px; background: var(--emboss); }
  .back-brand__name {
    font-weight: 900;
    font-size: 34px;
    letter-spacing: 1px;
    color: var(--emboss-light);
    text-transform: uppercase;
  }
</style>
</head>
<body>
  <section class="card card--front" aria-label="Business card front">
    <div class="brand">
      <span class="brand__mark"></span>
      <span class="brand__name">Ridgeline Design + Build</span>
    </div>

    <div class="person">
      <p class="person__name">Daniel Mercer</p>
      <p class="person__title">Owner</p>
    </div>

    <div class="divider"></div>

    <div class="contacts">
      <div class="contacts__col">
        <span class="contact">
          <svg viewBox="0 0 16 16" aria-hidden="true"><path d="M3 1h3l1.5 4-2 1.2a9 9 0 0 0 4.3 4.3L11 8.5l4 1.5v3a2 2 0 0 1-2 2A12 12 0 0 1 1 3a2 2 0 0 1 2-2z"/></svg>
          021-555 0142
        </span>
        <span class="contact">
          <svg viewBox="0 0 16 16" aria-hidden="true"><path d="M4 0h8a1.5 1.5 0 0 1 1.5 1.5v13A1.5 1.5 0 0 1 12 16H4a1.5 1.5 0 0 1-1.5-1.5v-13A1.5 1.5 0 0 1 4 0zm0 2v10h8V2zm4 11a1 1 0 1 0 0 2 1 1 0 0 0 0-2z"/></svg>
          021-555 0187
        </span>
      </div>
      <div class="contacts__col">
        <span class="contact">
          <svg viewBox="0 0 16 16" aria-hidden="true"><path d="M0 3h16v10H0zm1.5 1.5L8 9l6.5-4.5V4h-13z"/></svg>
          office@ridgeline.co
        </span>
        <span class="contact">
          <svg viewBox="0 0 16 16" aria-hidden="true"><path d="M8 0a8 8 0 1 0 0 16A8 8 0 0 0 8 0zm0 1.6c.9 0 2 1.7 2.4 4.4H5.6C6 3.3 7.1 1.6 8 1.6zM1.7 7.4h2.5a16 16 0 0 0 0 1.2H1.7zm4 0h4.6a14 14 0 0 1 0 1.2H5.7zm6.1 0h2.5v1.2h-2.5a16 16 0 0 0 0-1.2zM5.6 10h4.8c-.4 2.7-1.5 4.4-2.4 4.4S6 12.7 5.6 10z"/></svg>
          www.ridgeline.co
        </span>
      </div>
      <div class="contacts__col">
        <span class="contact">18 Quarry Road, Unit 4</span>
        <span class="contact">30117, Northland</span>
      </div>
    </div>

    <div class="edge-band"></div>
  </section>

  <section class="card card--back" aria-label="Business card back">
    <div class="back-brand">
      <span class="back-brand__mark"></span>
      <span class="back-brand__name">Ridgeline</span>
    </div>
  </section>
</body>
</html>
```